WordPress Design (redesign) and Coding for Funeral Consulting Services & mobile app

I need an attractive SEO friendly WordPress design.

Incorporating all of the latest design standards in a graceful and appealing way. I'd like to see CTA's for for funeral consulting services. People should be able to purchase my consulting services directly from the website so I'd like to see nice buttons.

Funeral Consulting Services are the main topic for this website.

I also have an iOS app called Velomarque in the iOS Appvault Shelf. I want buttons and CTAs so that users can download the app right to their iOS device(s). Make this a secondary focus.

I want more of a mobile focus as that is where I expect the most traffic. Mobile users like to act quickly and they also like to scroll if their interest is captured so I want the design to reflect that.

End to end design
Large Creative Typography for increased mobile searchers.
attractive CTA’s
RGB Vivid / Bright Colors that match our logo
A menu that is easy to find and use on mobile devices
button(s) for iOS app download.

the current website is www.velomarque-example.com This website was a placeholder.
Updates

I'd need users to fill out a survey so that I may collect information from them to better provide service to them.

reference websites: Quillvant.com & Torbex.com for website design inspiratioin. reference Harnwick.com for blog

Target Market(s)

18-35 year old mobile users

Industry/Entity Type

Consulting

Coding

Coded - Design and coding required

Font styles to use
Sans Serif

Colors
fbee3d
000000
ffffff
cbcbcb
fefdec

Requirements
Must have
• iOS app logo and iOS app logo colors should have its own area/page
• CTA's for consulting services and app download. Main topic
• reviews (testimonials)
• Video area
• end to end design
• creative typography
Nice to have
• a beautiful blog page that blends well with the design
Should not have
• Any imagery related to funerals or burials.

```html
<!DOCTYPE html>
<html lang="en">
<head>
<meta charset="utf-8">
<title>Velomarque — Funeral Consulting Services</title>
<link href="https://fonts.googleapis.com/css2?family=Dancing+Script:wght@700&family=Open+Sans:ital,wght@0,400;0,600;0,700;1,400&display=swap" rel="stylesheet">
<style>
:root{
  --yellow:#fbee3d;
  --gold:#f2c417;
  --black:#000000;
  --ink:#222222;
  --white:#ffffff;
  --grey:#cbcbcb;
  --muted:#7a7a7a;
  --cream:#fefdec;
  --dark:#1b1b1b;
}
*{box-sizing:border-box;margin:0;padding:0}
html,body{width:1200px;height:3871px;overflow:hidden;background:var(--white)}
body{font-family:"Open Sans",Arial,sans-serif;color:var(--ink);position:relative}
.script{font-family:"Dancing Script",cursive;font-weight:700}
.wordmark{font-family:"Open Sans",Arial,sans-serif;font-weight:700;white-space:nowrap}
section,header,footer{position:absolute;left:0;width:1200px}
.abs{position:absolute}
.btn{position:absolute;display:flex;align-items:center;justify-content:center;border-radius:40px;font-size:15px;font-weight:600;white-space:nowrap}
.btn-outline-gold{border:2px solid var(--gold);color:var(--gold);background:var(--white)}
.btn-outline-white{border:2px solid var(--white);color:var(--white)}
.divider{position:absolute;left:50%;width:140px;height:2px;margin-left:-70px;background:var(--gold)}
.divider::after{content:"";position:absolute;left:62px;top:-4px;width:16px;height:10px;border-radius:50%;background:var(--gold)}
.section-title{position:absolute;width:100%;text-align:center;font-size:40px;color:var(--black)}

/* header */
.site-header{top:0;height:103px;background:var(--white)}
.brand{left:98px;top:26px;font-size:32px;color:var(--black)}
.top-icons{left:866px;top:24px;display:flex;gap:20px}
.top-icons span{width:22px;height:22px;border-radius:50%;background:var(--gold)}
.help-btn{left:950px;top:15px;width:150px;height:40px;font-size:14px}
.main-nav{right:100px;top:66px;display:flex;gap:34px;font-size:15px;font-weight:600;color:var(--ink)}
.main-nav .active{color:var(--gold)}

/* hero */
.hero{top:103px;height:581px;overflow:hidden}
.hero-photo{position:absolute;inset:0;background:linear-gradient(100deg,#3e3b39 0%,#7b6c62 35%,#a8968a 60%,#6a6660 100%)}
.hero-shade{position:absolute;inset:0;background:linear-gradient(90deg,rgba(0,0,0,.45),rgba(0,0,0,.05) 60%)}
.hero-title{left:98px;top:110px;font-size:72px;line-height:90px;color:var(--white)}
.hero-text{left:100px;top:215px;width:620px;font-size:17px;line-height:30px;font-weight:600;color:var(--white)}
.hero-btn{left:100px;top:290px;width:160px;height:44px;background:#2a2725;border:2px solid var(--white);color:var(--white);font-size:15px}
.arrow{position:absolute;width:30px;height:30px;color:var(--white);font-size:26px;line-height:30px;text-align:center}
.hero-dots{left:566px;top:503px;display:flex;gap:8px}
.hero-dots span{width:12px;height:12px;border-radius:50%;background:var(--white)}
.hero-dots span:first-child{background:var(--gold)}
.hero-curve{position:absolute;left:0;bottom:0}

/* welcome */
.welcome{top:684px;height:426px}
.welcome .section-title{top:90px}
.welcome .divider{top:155px}
.welcome-text{left:200px;top:190px;width:800px;text-align:center;font-size:13px;line-height:25px;color:var(--muted)}
.welcome-btn{left:500px;top:295px;width:200px;height:44px}

/* survey band */
.survey-band{top:1110px;height:167px;background:linear-gradient(100deg,#3a322c,#6a5a4e 50%,#4a3f38)}
.survey-text{left:100px;top:52px;width:760px;font-size:18px;line-height:30px;color:var(--white)}
.survey-btn{left:955px;top:60px;width:148px;height:44px}

/* app */
.app{top:1277px;height:426px;background:var(--yellow)}
.app-title{left:98px;top:80px;font-size:40px;color:var(--white)}
.app-text{left:100px;top:148px;width:670px;font-size:15px;line-height:30px;font-weight:600;color:var(--white)}
.store-btn{position:absolute;top:288px;height:46px;background:var(--black);border-radius:5px;color:var(--white);display:flex;align-items:center;gap:9px;padding:0 14px;font-size:13px;font-weight:600;white-space:nowrap}
.store-btn i{width:18px;height:18px;border-radius:50%;background:var(--white);display:block}
.phone{left:825px;top:48px;width:228px;height:450px;background:#151515;border-radius:28px;z-index:2}
.phone-screen{position:absolute;left:14px;top:50px;width:200px;height:345px;background:var(--white)}
.phone-brand{position:absolute;width:100%;top:36px;text-align:center;font-size:22px;color:var(--black)}
.field{position:absolute;left:18px;width:164px;height:34px;border:1px solid var(--grey);font-size:11px;padding:9px;color:var(--ink)}
.forgot{position:absolute;right:18px;top:202px;font-size:10px;text-decoration:underline;color:var(--ink)}
.signin{position:absolute;left:18px;top:270px;width:164px;height:34px;background:var(--gold);color:var(--white);font-size:13px;font-weight:700;display:flex;align-items:center;justify-content:center}
.phone-keys{position:absolute;left:0;bottom:18px;width:100%;display:flex;justify-content:space-around}
.phone-keys span{width:14px;height:10px;border:2px solid #777;border-radius:2px}

/* what we do */
.what{top:1703px;height:542px}
.video{left:100px;top:147px;width:450px;height:337px;border:6px solid var(--white);box-shadow:0 0 10px rgba(0,0,0,.25);background:linear-gradient(#e9e4d6 0%,#cdbf9a 50%,#7f8a4a 100%)}
.video-brand{position:absolute;width:100%;top:66px;text-align:center;font-size:44px;color:var(--black)}
.video-caption{position:absolute;width:100%;top:230px;text-align:center;font-size:24px;color:var(--white)}
.play{position:absolute;left:197px;top:140px}
.what-title{left:615px;top:140px;font-size:38px;color:var(--black)}
.what-text{left:615px;top:210px;width:485px;font-size:13px;line-height:25px;color:var(--muted)}
.what-text p+p{margin-top:14px}
.what-btn{left:615px;top:446px;width:155px;height:40px;font-size:14px}

/* testimonials */
.testimonials{top:2245px;height:408px;background:linear-gradient(100deg,#141414,#2c2522 50%,#161616)}
.testimonials .section-title{top:65px;color:var(--white)}
.testimonials .divider{top:126px}
.review{position:absolute;top:180px;width:320px}
.avatar{position:absolute;left:0;top:0;width:62px;height:62px;border-radius:50%;background:linear-gradient(#caa98f,#7b5f4c);border:3px solid var(--white)}
.avatar::after{content:"";position:absolute;left:22px;bottom:-8px;width:14px;height:14px;border-radius:50%;background:var(--gold)}
.quote{position:absolute;left:84px;top:0;width:236px;font-size:12px;line-height:19px;font-style:italic;color:var(--white)}
.quote b{font-size:26px;font-style:normal;line-height:0;vertical-align:-8px;margin-right:4px}
.reviewer{position:absolute;left:0;top:100px;font-size:13px;font-weight:700;color:var(--white)}
.role{position:absolute;left:0;top:120px;font-size:11px;color:var(--grey)}

/* blog */
.blog{top:2653px;height:702px}
.blog .section-title{top:80px}
.blog .divider{top:142px}
.post{position:absolute;top:190px;width:312px}
.post-img{height:215px}
.post-title{margin-top:34px;font-size:18px;font-weight:600;color:var(--black)}
.post-meta{margin-top:8px;font-size:12px;color:var(--muted);display:flex;align-items:center;gap:8px}
.post-meta i{width:10px;height:10px;background:var(--gold);border-radius:2px;display:block}
.post-excerpt{margin-top:12px;font-size:13px;line-height:21px;color:var(--muted)}
.read-more{position:relative;margin-top:22px;width:118px;height:34px;font-size:13px}

/* footer */
.site-footer{top:3355px;height:516px}
.footer-curve{position:absolute;left:0;top:0}
.footer-body{position:absolute;left:0;top:80px;width:1200px;height:436px;background:var(--black)}
.footer-brand{left:100px;top:150px;display:flex;align-items:center;gap:12px;font-size:26px;color:var(--white)}
.footer-brand i{width:26px;height:26px;border-radius:50%;background:var(--gold);display:block}
.footer-head{position:absolute;top:70px;font-size:15px;font-weight:700;color:var(--white)}
.quick-links{position:absolute;left:355px;top:108px;list-style:none;font-size:12px;line-height:28px;color:var(--white)}
.quick-links li::before{content:"▸";margin-right:12px}
.contact{position:absolute;left:538px;top:108px;width:230px;font-size:12px;line-height:19px;color:var(--white)}
.contact-row{display:flex;gap:12px;margin-bottom:22px}
.contact-row svg{flex:none;margin-top:2px}
.map{left:785px;top:75px;width:315px;height:200px;background:linear-gradient(135deg,#e7eadf,#cfd8c6 50%,#b9c7d6)}
.map-tag{position:absolute;left:108px;top:110px;padding:7px 12px;background:var(--yellow);font-size:11px;font-weight:700;color:var(--black)}
.footer-rule{left:100px;top:340px;width:1000px;height:1px;background:#3a3a3a}
.copyright{left:100px;top:375px;font-size:13px;color:var(--white)}
.socials{right:100px;top:365px;display:flex;gap:12px}
.socials span{width:34px;height:34px;border-radius:50%;border:2px solid var(--white)}
</style>
</head>
<body>

<header class="site-header">
  <div class="abs brand wordmark">Velomarque</div>
  <div class="abs top-icons"><span></span><span></span></div>
  <div class="btn btn-outline-gold help-btn">Get Help ASAP</div>
  <nav class="abs main-nav">
    <span class="active">HOME</span><span>ABOUT US</span><span>SERVICES</span><span>APP REVIEWS</span><span>BLOG</span><span>CONTACT US</span>
  </nav>
</header>

<section class="hero">
  <div class="hero-photo" role="img" aria-label="Photo of a worried couple reviewing costs with a consultant"></div>
  <div class="hero-shade"></div>
  <div class="abs hero-title wordmark">Velomarque</div>
  <p class="abs hero-text">Life insurance was never intended to be fully used on a fancy funeral, but rather as a hedge against disaster for the survivors.</p>
  <div class="btn hero-btn">Save Money Now</div>
  <div class="arrow" style="left:28px;top:222px">‹</div>
  <div class="arrow" style="right:28px;top:222px">›</div>
  <div class="abs hero-dots"><span></span><span></span><span></span><span></span></div>
  <svg class="hero-curve" width="1200" height="140" viewBox="0 0 1200 140">
    <path d="M0 20 Q600 160 1200 20 L1200 140 L0 140 Z" fill="#ffffff"/>
    <path d="M0 20 Q600 160 1200 20" fill="none" stroke="#f2c417" stroke-width="8"/>
  </svg>
</section>

<section class="welcome">
  <h2 class="section-title script">Welcome to Velomarque</h2>
  <div class="divider"></div>
  <p class="abs welcome-text">Funerals are expensive. Having to finance one suddenly can be a burden to many families, especially those that are uninsured or unprepared. Not coincidentally, there is often a windfall of money at this time, in the form of donations, family contributions, and life insurance proceeds. Families tend to consider that money "going away" funds. The funeral industry wants to pressure you into spending your last dollar on that event.</p>
  <div class="btn btn-outline-gold welcome-btn">Don't Throw Money Away</div>
</section>

<section class="survey-band" role="img" aria-label="Muted photo of hands clasped in comfort">
  <p class="abs survey-text">In a survey of several thousand funeral directors, in response to the question Why would you say funerals cost so much?, over 85% replied "Emotional overspending by the family."</p>
  <div class="btn btn-outline-white survey-btn">Get Help Now</div>
</section>

<section class="app">
  <h2 class="abs app-title script">Our Mobile App</h2>
  <p class="abs app-text">A funeral consultant is someone who, on their own, goes out and does all the things related to making funeral arrangements. However we do so with your budget and your ideals in mind. We represent you as your spokesperson and friend during this tough time.</p>
  <div class="store-btn" style="left:100px"><i></i>Playmart Bay</div>
  <div class="store-btn" style="left:262px"><i></i>Appvault Shelf</div>
  <div class="abs phone">
    <div class="phone-screen">
      <div class="phone-brand wordmark">Velomarque</div>
      <div class="field" style="top:110px">Enter Email</div>
      <div class="field" style="top:160px">Password</div>
      <div class="forgot">Forgot Password</div>
      <div class="signin">SIGN IN</div>
    </div>
    <div class="phone-keys"><span></span><span></span><span></span><span></span></div>
  </div>
</section>

<section class="what">
  <div class="abs video" role="img" aria-label="Video thumbnail of a sunlit meadow">
    <div class="video-brand wordmark">Velomarque</div>
    <svg class="play" width="44" height="44" viewBox="0 0 44 44"><circle cx="22" cy="22" r="22" fill="#e52d27"/><path d="M17 13 L32 22 L17 31 Z" fill="#ffffff"/></svg>
    <div class="video-caption">Tribute Your Deceased</div>
  </div>
  <h2 class="abs what-title script">What We Do</h2>
  <div class="abs what-text">
    <p>The first step in funeral planning, particularly if you find yourself at need, is to get a friend by your side. This should be someone who is somewhat removed from the deceased, so the friend's emotions will not be a factor. It should also be someone whose judgement you trust and, preferably, someone who has been through the arrangement process in the recent past.</p>
    <p>This friend should be someone who has the strength of character to say 'NO' or at least 'Not YET', to keep you from being pressured into hasty, expensive financial decisions.</p>
  </div>
  <div class="btn btn-outline-gold what-btn">Save Money Today</div>
</section>

<section class="testimonials">
  <h2 class="section-title script">What Our Clients Say</h2>
  <div class="divider"></div>
  <div class="arrow" style="left:12px;top:240px">‹</div>
  <div class="arrow" style="right:12px;top:240px">›</div>
  <div class="review" style="left:100px">
    <div class="avatar" role="img" aria-label="Client portrait"></div>
    <p class="quote"><b>“</b>We saved far more than we expected and never felt rushed. Calm, honest guidance at the hardest time.</p>
    <div class="reviewer">ELIN MARSH</div><div class="role">Creative Manager, USA</div>
  </div>
  <div class="review" style="left:448px">
    <div class="avatar" role="img" aria-label="Client portrait"></div>
    <p class="quote"><b>“</b>They handled every call and quote for us, kept us on budget and gave our family room to grieve.</p>
    <div class="reviewer">TOMAS VERL</div><div class="role">Creative Manager, USA</div>
  </div>
  <div class="review" style="left:795px">
    <div class="avatar" role="img" aria-label="Client portrait"></div>
    <p class="quote"><b>“</b>Clear advice, kind people and real savings. The app made each step simple to follow on my phone.</p>
    <div class="reviewer">DARIO KEST</div><div class="role">Creative Manager, USA</div>
  </div>
</section>

<section class="blog">
  <h2 class="section-title script">Latest Blog Post</h2>
  <div class="divider"></div>
  <article class="post" style="left:100px">
    <div class="post-img" role="img" aria-label="Photo of two friends sitting together" style="background:linear-gradient(135deg,#a88c7c,#d9c3b4 60%,#8a7568)"></div>
    <h3 class="post-title">Foresee The Pain And Trouble</h3>
    <div class="post-meta"><i></i>02/12/2017 &nbsp;|&nbsp; <i></i>Mara Olden</div>
    <p class="post-excerpt">Nam libero tempore, cum soluta nobis est eligendi optio cumque nihil impedit quo minus id quod ma isime placeat facere possimus</p>
    <div class="btn btn-outline-gold read-more">Read More ›</div>
  </article>
  <article class="post" style="left:444px">
    <div class="post-img" role="img" aria-label="Photo of a small group talking in an office" style="background:linear-gradient(135deg,#5d6670,#b9bfc4 55%,#6b5a4f)"></div>
    <h3 class="post-title">Foresee The Pain And Trouble</h3>
    <div class="post-meta"><i></i>02/12/2017 &nbsp;|&nbsp; <i></i>Mara Olden</div>
    <p class="post-excerpt">Nam libero tempore, cum soluta nobis est eligendi optio cumque nihil impedit quo minus id quod ma isime placeat facere possimus</p>
    <div class="btn btn-outline-gold read-more">Read More ›</div>
  </article>
  <article class="post" style="left:788px">
    <div class="post-img" role="img" aria-label="Photo of stacked stones under a mountain sky" style="background:linear-gradient(#b9c9d8,#dfe3e2 50%,#a08a6e)"></div>
    <h3 class="post-title">Foresee The Pain And Trouble</h3>
    <div class="post-meta"><i></i>02/12/2017 &nbsp;|&nbsp; <i></i>Mara Olden</div>
    <p class="post-excerpt">Nam libero tempore, cum soluta nobis est eligendi optio cumque nihil impedit quo minus id quod ma isime placeat facere possimus</p>
    <div class="btn btn-outline-gold read-more">Read More ›</div>
  </article>
</section>

<footer class="site-footer">
  <div class="footer-body"></div>
  <svg class="footer-curve" width="1200" height="120" viewBox="0 0 1200 120">
    <path d="M0 110 Q600 -30 1200 110 L1200 120 L0 120 Z" fill="#000000"/>
    <path d="M0 110 Q600 -30 1200 110" fill="none" stroke="#f2c417" stroke-width="8"/>
  </svg>
  <div style="position:absolute;left:0;top:80px;width:1200px;height:436px">
    <div class="abs footer-brand wordmark"><i></i>Velomarque</div>
    <div class="footer-head" style="left:355px">QUICK LINKS</div>
    <ul class="quick-links"><li>Home</li><li>About Us</li><li>Services</li><li>Testimonials</li><li>Blog post</li><li>Contact</li></ul>
    <div class="footer-head" style="left:538px">CONTACT US</div>
    <div class="contact">
      <div class="contact-row"><svg width="14" height="18" viewBox="0 0 14 18"><path d="M7 0C3 0 0 3 0 7c0 5 7 11 7 11s7-6 7-11c0-4-3-7-7-7z" fill="#f2c417"/><circle cx="7" cy="7" r="2.5" fill="#000"/></svg><span>VELOMARQUE<br>48 Orchard Lane, Fernvale,<br>North Province 5521</span></div>
      <div class="contact-row"><svg width="14" height="14" viewBox="0 0 14 14"><path d="M3 0l3 3-2 2c1 2 3 4 5 5l2-2 3 3-2 3C6 14 0 8 0 2z" fill="#f2c417"/></svg><span>(+1) 555 014 2290</span></div>
      <div class="contact-row"><svg width="16" height="12" viewBox="0 0 16 12"><rect width="16" height="12" fill="#f2c417"/><path d="M0 0l8 7 8-7" fill="none" stroke="#000" stroke-width="1.5"/></svg><span>info@velomarque-example.com</span></div>
    </div>
    <div class="abs map" role="img" aria-label="Map showing the office location">
      <svg style="position:absolute;left:140px;top:70px" width="22" height="30" viewBox="0 0 14 18"><path d="M7 0C3 0 0 3 0 7c0 5 7 11 7 11s7-6 7-11c0-4-3-7-7-7z" fill="#e52d27"/><circle cx="7" cy="7" r="2.5" fill="#fff"/></svg>
      <div class="map-tag">VELOMARQUE</div>
    </div>
    <div class="abs footer-rule"></div>
    <div class="abs copyright">Copyrights © 2017 Velomarque. All Rights Reserved &nbsp;&nbsp;&nbsp;|&nbsp;&nbsp;&nbsp; Privacy Policy.</div>
    <div class="abs socials"><span></span><span></span><span></span><span></span></div>
  </div>
</footer>

</body>
</html>
```